Moon Tot needs ecommerce website design help

We need someone to set up a fully functional website for us. We sell baby bibs, I attached them along with our company logo (MTG: moon tot goods). The bibs are made of 100% silicon, they are safe, light weight, soft, smooth, flexible, dishwasher safe and has funny faces.

Business name: Moon Tot Goods
Elm Hollow, NY 00000
email: MoonTotGoods@mailbox-example.com
tel.: (555) 014-TOTS
website: MoonTotGoods-example.com

Target Market(s)

18-40

Industry/Entity Type

Baby

Coding

Coded - Design and coding required

Number of Pages Required

5+ page

Requirements
Must have
• 1. Pages: Why buy from us, Contact Us, Home page, Products Page, Blog
• 2. Use the colors from our logo for the web design.
• 3. Need a link that will connect visitors to our facebook, instagram, Pinterest and Tumblr account. Would like links on,the top left side of the page
Nice to have
• My Cart page
• 1. On contact us page, we want to include some type of template for the customer to complete. (Ex: name, email address, contact number, optional home address, comments)
• 2. When clients visit our website, we want a capture/pop up for the customer to subscribe to our email list to receive discounts. (Ex. Want 10% off your next order ? Suscribe to our mailing list below and get a 10% off code to use at check out. If they don't want to subscribe, they have the option to select "No Thank You, I want to pay full price).
• 3. On home page have subscribe to our email list.

```html
<!DOCTYPE html>
<html lang="en">
<head>
<meta charset="utf-8">
<title>Moon Tot Goods – Silicone Baby Bibs</title>
<link href="https://fonts.googleapis.com/css2?family=Oswald:wght@400;600&family=Open+Sans:wght@400;600;700&display=swap" rel="stylesheet">
<style>
:root{
  --pink:#f27aaa;
  --pink-dark:#e35d95;
  --pink-soft:#fbd3e3;
  --pink-pale:#fdeef4;
  --green:#8cc63f;
  --green-dark:#6fa828;
  --orange:#f6a55a;
  --blue:#7cc3e8;
  --yellow:#f7d250;
  --ink:#555;
  --muted:#999;
  --line:#e6e6e6;
  --white:#fff;
}
*{box-sizing:border-box;margin:0;padding:0}
html,body{width:768px;height:1200px;overflow:hidden;background:var(--white)}
body{position:relative;font-family:"Open Sans",Arial,sans-serif;color:var(--ink);font-size:9px}
.abs{position:absolute}
.heading{font-family:"Oswald","Arial Narrow",sans-serif;text-transform:uppercase;letter-spacing:.5px;font-weight:400}

/* header */
.brand{left:64px;top:22px;font-weight:700;font-size:20px;color:var(--pink);display:flex;align-items:center;gap:8px}
.brand-dot{width:22px;height:22px;border-radius:50%;background:var(--green)}
.social{display:flex;gap:6px}
.social span{width:18px;height:18px;border-radius:50%;display:block}
.header-social{left:604px;top:18px}
.nav{left:307px;top:50px;display:flex;gap:4px}
.nav a{display:block;width:72px;height:28px;line-height:28px;text-align:center;color:var(--white);font-weight:600;font-size:9px;text-decoration:none;border-radius:6px 6px 0 0}

/* hero */
.hero{left:64px;top:90px;width:640px;height:320px;background:
  radial-gradient(ellipse 180px 150px at 300px 130px,#f1e3cf 0%,#e7cfb4 40%,rgba(231,207,180,0) 75%),
  radial-gradient(ellipse 260px 200px at 110px 230px,#f3c7d6 0%,rgba(243,199,214,0) 70%),
  linear-gradient(110deg,#c9cf83 0%,#d8d98f 40%,#b9c86a 75%,#a9bd5c 100%)}
.hero-title{left:520px;top:230px;font-size:30px;color:var(--white);font-weight:600}
.hero-text{left:520px;top:278px;width:170px;color:var(--white);font-size:9px;line-height:1.5}
.hero-btn{left:520px;top:322px;width:70px;height:20px;background:var(--pink);color:var(--white);font-size:8px;font-weight:700;text-align:center;line-height:20px}

/* newsletter band */
.band{left:64px;top:418px;width:640px;height:62px;background:var(--pink)}
.band-badge{left:80px;top:430px;width:38px;height:38px;border:2px solid var(--white);border-radius:50%;color:var(--white);font-size:15px;text-align:center;line-height:34px;font-weight:700}
.band-title{left:132px;top:438px;color:var(--white);font-size:16px;font-weight:600}
.band-input{left:300px;top:438px;width:300px;height:24px;background:var(--white);border-radius:2px}
.band-btn{left:612px;top:438px;width:78px;height:24px;background:var(--pink-soft);color:var(--pink-dark);font-weight:700;font-size:8px;line-height:24px;text-align:center}

/* sidebar */
.side-head{width:187px;height:22px;background:var(--pink);color:var(--white);font-size:10px;line-height:22px;padding-left:8px}
.quotes{left:64px;top:530px;width:187px;display:flex;flex-direction:column;gap:6px}
.quote{display:flex;gap:6px;align-items:center;font-size:7px;color:var(--muted);line-height:1.3}
.quote i{width:20px;height:20px;border-radius:50%;flex:none;display:block}
.thumbs{left:64px;top:586px;width:187px;display:grid;grid-template-columns:repeat(3,1fr);gap:6px}
.thumbs span{display:block;height:46px}
.promo{left:64px;top:720px;width:187px;height:100px;background:
  radial-gradient(circle at 150px 40px,#f5c1a0 0%,rgba(245,193,160,0) 55%),
  linear-gradient(120deg,#d9a48f,#ee8fb2)}
.promo-text{left:76px;top:752px;color:var(--white);font-size:24px;font-weight:600;line-height:1}
.mini{left:64px;width:187px;height:60px}
.mini-img{left:0;top:8px;width:46px;height:46px;border-radius:8px}
.mini-name{left:56px;top:14px;font-size:8px;color:var(--pink-dark);font-weight:700}
.mini-price{left:56px;top:30px;font-size:8px;color:var(--muted)}

/* products */
.section-title{left:269px;top:503px;font-size:16px;color:var(--pink)}
.arrows{left:664px;top:510px;display:flex;gap:4px}
.arrows span{width:16px;height:14px;background:var(--pink-soft);display:block}
.arrows span:last-child{background:var(--pink)}
.card{width:138px;height:200px;border:1px solid var(--line);background:var(--white)}
.card-img{left:24px;top:14px;width:90px;height:100px;border-radius:40px 40px 45px 45px}
.card-name{left:10px;top:130px;font-size:8px;color:var(--pink-dark);font-weight:700}
.card-price{left:10px;top:146px;font-size:8px;color:var(--muted)}
.card-btn{left:10px;top:166px;width:56px;height:18px;background:var(--green);color:var(--white);font-size:7px;font-weight:700;line-height:18px;text-align:center}
.tag{left:0;top:0;width:30px;height:30px;border-radius:50%;background:var(--green);color:var(--white);font-size:7px;line-height:30px;text-align:center;font-weight:700}

.feature{display:flex;align-items:center;gap:10px;top:962px}
.feature-icon{width:48px;height:48px;border-radius:50%;display:flex;align-items:center;justify-content:center}
.feature-text b{display:block;font-size:9px;color:var(--pink-dark)}
.feature-text span{font-size:8px;color:var(--muted)}

/* footer */
.footer{left:0;top:1040px;width:768px;height:160px}
.footer-row{left:80px;top:1100px;display:flex;gap:60px;color:var(--white);font-size:8px}
.footer-item{display:flex;gap:8px;align-items:center}
.footer-social{left:600px;top:1104px}
.footer-social span{background:var(--white);opacity:.85}
.copyright{left:0;top:1170px;width:768px;height:30px;background:var(--pink-dark);color:var(--white);text-align:center;line-height:30px;font-size:8px}

/* overlay + popup */
.veil{left:0;top:0;width:768px;height:1200px;background:rgba(255,255,255,.42)}
.popup{left:250px;top:192px;width:300px;height:256px;background:var(--white);box-shadow:0 4px 20px rgba(0,0,0,.18)}
.popup-close{left:268px;top:12px;width:16px;height:16px;border-radius:50%;background:var(--pink);color:var(--white);font-size:11px;line-height:15px;text-align:center}
.popup-kicker{left:0;top:30px;width:300px;text-align:center;color:var(--pink);font-size:11px}
.popup-title{left:0;top:44px;width:300px;text-align:center;color:var(--pink-dark);font-size:23px;font-weight:600}
.field{left:22px;width:256px;height:24px;border:1px solid #ddd;font-size:8px;color:#aaa;line-height:22px;padding-left:8px}
.field-select::after{content:"";position:absolute;right:0;top:0;width:22px;height:22px;background:#eee}
.popup-btn{left:14px;top:190px;width:272px;height:28px;background:linear-gradient(var(--green),var(--green-dark));color:var(--white);font-weight:700;font-size:11px;line-height:28px;text-align:center}
</style>
</head>
<body>

<header>
  <div class="abs brand"><span class="brand-dot"></span>Moon Tot Goods</div>
  <div class="abs social header-social">
    <span style="background:var(--green)"></span><span style="background:var(--orange)"></span><span style="background:var(--pink)"></span><span style="background:var(--blue)"></span>
  </div>
  <nav class="abs nav">
    <a style="background:var(--green)">HOME</a>
    <a style="background:var(--pink)">PRODUCTS</a>
    <a style="background:var(--orange)">WHY US</a>
    <a style="background:var(--blue)">BLOG</a>
    <a style="background:var(--yellow)">CONTACT</a>
  </nav>
</header>

<section>
  <div class="abs hero" role="img" aria-label="Photo of a baby wearing a silicone bib at mealtime"></div>
  <div class="abs hero-title heading">Moon Baby</div>
  <div class="abs hero-text">Soft, safe silicone bibs with funny faces for happy meals.</div>
  <div class="abs hero-btn">SHOP NOW</div>
</section>

<section>
  <div class="abs band"></div>
  <div class="abs band-badge">25</div>
  <div class="abs band-title heading">Newsletter Signup</div>
  <div class="abs band-input"></div>
  <div class="abs band-btn">SUBSCRIBE</div>
</section>

<aside>
  <div class="abs side-head heading" style="left:64px;top:500px">Testimonials &amp; Instagram</div>
  <div class="abs quotes">
    <div class="quote"><i style="background:#f3c9b8" role="img" aria-label="Customer photo"></i><span>“Easy to wash, my son loves it.”<br>– Anna K.</span></div>
    <div class="quote"><i style="background:#cfe3ef" role="img" aria-label="Customer photo"></i><span>“Soft, light and so cute!”<br>– Lisa M.</span></div>
  </div>
  <div class="abs thumbs" role="img" aria-label="Instagram photos of babies wearing bibs">
    <span style="background:linear-gradient(135deg,#d9e8b8,#f2c9a9)"></span>
    <span style="background:linear-gradient(135deg,#f6c2d6,#f3dcc4)"></span>
    <span style="background:linear-gradient(135deg,#bfdcef,#efd8c6)"></span>
    <span style="background:linear-gradient(135deg,#f1d9c3,#c9e3a4)"></span>
    <span style="background:linear-gradient(135deg,#f5e39c,#f1c7b5)"></span>
    <span style="background:linear-gradient(135deg,#c4e0ef,#f6c7d8)"></span>
  </div>
  <div class="abs promo" role="img" aria-label="Promotional photo of a baby with a bib"></div>
  <div class="abs promo-text heading">Up to save<br>30%</div>
  <div class="abs side-head heading" style="left:64px;top:832px">Coming Soon</div>
  <div class="abs mini" style="top:866px">
    <div class="abs mini-img" style="background:linear-gradient(160deg,#f7b3cf,#ee85b0)" role="img" aria-label="Pink bib coming soon"></div>
    <div class="abs mini-name">Moon bib silicone</div>
    <div class="abs mini-price">$12.00</div>
  </div>
  <div class="abs mini" style="top:940px">
    <div class="abs mini-img" style="background:linear-gradient(160deg,#f7b3cf,#ee85b0)" role="img" aria-label="Pink bib coming soon"></div>
    <div class="abs mini-name">Star bib silicone</div>
    <div class="abs mini-price">$12.00</div>
  </div>
</aside>

<main>
  <h2 class="abs section-title heading">Features of the Product</h2>
  <div class="abs arrows"><span></span><span></span></div>

  <div class="abs card" style="left:269px;top:525px"><div class="abs card-img" style="background:linear-gradient(160deg,#f7b8d2,#ec7fae)" role="img" aria-label="Pink silicone bib"></div><div class="abs tag">NEW</div><div class="abs card-name">Pink silicone bib</div><div class="abs card-price">$12.00</div><div class="abs card-btn">ADD TO CART</div></div>
  <div class="abs card" style="left:417px;top:525px"><div class="abs card-img" style="background:linear-gradient(160deg,#aedaf2,#5fb2e2)" role="img" aria-label="Blue silicone bib"></div><div class="abs card-name">Blue silicone bib</div><div class="abs card-price">$12.00</div><div class="abs card-btn">ADD TO CART</div></div>
  <div class="abs card" style="left:565px;top:525px"><div class="abs card-img" style="background:linear-gradient(160deg,#c6e59c,#8cc63f)" role="img" aria-label="Green silicone bib"></div><div class="abs card-name">Green silicone bib</div><div class="abs card-price">$12.00</div><div class="abs card-btn">ADD TO CART</div></div>
  <div class="abs card" style="left:269px;top:735px"><div class="abs card-img" style="background:linear-gradient(160deg,#fbcf9c,#f4a24e)" role="img" aria-label="Orange silicone bib"></div><div class="abs tag">NEW</div><div class="abs card-name">Orange silicone bib</div><div class="abs card-price">$12.00</div><div class="abs card-btn">ADD TO CART</div></div>
  <div class="abs card" style="left:417px;top:735px"><div class="abs card-img" style="background:linear-gradient(160deg,#9fd3f0,#4aa6dc)" role="img" aria-label="Sky blue silicone bib"></div><div class="abs card-name">Sky silicone bib</div><div class="abs card-price">$12.00</div><div class="abs card-btn">ADD TO CART</div></div>
  <div class="abs card" style="left:565px;top:735px"><div class="abs card-img" style="background:linear-gradient(160deg,#fbe79a,#f2cb3a)" role="img" aria-label="Yellow silicone bib"></div><div class="abs card-name">Yellow silicone bib</div><div class="abs card-price">$12.00</div><div class="abs card-btn">ADD TO CART</div></div>

  <div class="abs feature" style="left:290px"><span class="feature-icon" style="background:var(--green)"><svg width="20" height="20" viewBox="0 0 20 20"><path d="M4 10 L8 14 L16 5" fill="none" stroke="#fff" stroke-width="2.5"/></svg></span><div class="feature-text"><b>DISHWASHER SAFE</b><span>Easy to clean every day</span></div></div>
  <div class="abs feature" style="left:500px"><span class="feature-icon" style="background:var(--pink)"><svg width="20" height="20" viewBox="0 0 20 20"><path d="M4 10 L8 14 L16 5" fill="none" stroke="#fff" stroke-width="2.5"/></svg></span><div class="feature-text"><b>100% SILICONE</b><span>Soft, light and flexible</span></div></div>
</main>

<footer>
  <svg class="abs footer" viewBox="0 0 768 160" aria-hidden="true">
    <path d="M0 30 Q24 0 48 30 T96 30 T144 30 T192 30 T240 30 T288 30 T336 30 T384 30 T432 30 T480 30 T528 30 T576 30 T624 30 T672 30 T720 30 T768 30 V160 H0Z" fill="var(--pink)"/>
  </svg>
  <div class="abs footer-row">
    <div class="footer-item">
      <svg width="18" height="14" viewBox="0 0 18 14"><rect x="1" y="1" width="16" height="12" fill="none" stroke="#fff" stroke-width="1.5"/><path d="M1 1 L9 8 L17 1" fill="none" stroke="#fff" stroke-width="1.5"/></svg>
      <span>Email<br>MoonTotGoods@mailbox-example.com</span>
    </div>
    <div class="footer-item">
      <svg width="12" height="16" viewBox="0 0 12 16"><path d="M6 15 C2 9 1 7 1 5 A5 5 0 0 1 11 5 C11 7 10 9 6 15Z" fill="#fff"/></svg>
      <span>Address<br>Elm Hollow, NY 00000</span>
    </div>
    <div class="footer-item">
      <svg width="14" height="14" viewBox="0 0 14 14"><path d="M3 1 L5 4 L4 6 Q6 9 8 10 L10 9 L13 11 L11 13 Q4 12 1 3Z" fill="#fff"/></svg>
      <span>Phone<br>(555) 014-TOTS</span>
    </div>
  </div>
  <div class="abs social footer-social"><span></span><span></span><span></span><span></span></div>
  <div class="abs copyright">© Copyright 2015 MoonTotGoods-example.com. All rights reserved.</div>
</footer>

<div class="abs veil"></div>

<div class="abs popup" role="dialog" aria-label="Newsletter signup">
  <div class="abs popup-close">×</div>
  <div class="abs popup-kicker heading">10% off your next order</div>
  <div class="abs popup-title heading">Newsletter Signup</div>
  <div class="abs field" style="top:88px">Enter your Name</div>
  <div class="abs field" style="top:118px">Enter your email address</div>
  <div class="abs field field-select" style="top:150px">I want to pay full price</div>
  <div class="abs popup-btn">SUBSCRIBE NOW</div>
</div>

</body>
</html>
```